Home Remodeling company needs a business card design

we need a business card design for home remodeling company in hamilton county, indiana USA. we offers a wide range of construction services including whole house renovations, Design and Build Basements and Kitchen and Bathroom Remodeling . we would like to see designs for both site of business card that use the same color of the company logo and also including all information below :
1- Karim Feltous CEO / General Contractor
2- all company contacts Telephone numbers ( 1-888-DULOM-47 ) ( 317-555-0193) email address ( info@dulomhome.com) website ( www.dulomhome.com ) and social media logos (Facebook- twitter- google plus )
3- company logo
4- licensed . insured . bonded

```html
<!DOCTYPE html>
<html lang="en">
<head>
<meta charset="utf-8">
<title>Dulom Home Remodeling – Business Card</title>
<link rel="stylesheet" href="https://fonts.googleapis.com/css2?family=Lato:wght@300;400;700;900&display=swap">
<style>
  :root {
    --brand-red: #c9323d;
    --brand-red-dark: #b02631;
    --ink: #3a3a3c;
    --ink-soft: #5a5a5e;
    --paper: #ffffff;
    --stage: #e9e6e1;
    --rule: #c8c8c8;
  }
  html, body {
    margin: 0;
    padding: 0;
    width: 1200px;
    height: 950px;
    overflow: hidden;
    background: var(--stage);
    font-family: "Lato", sans-serif;
  }
  .canvas {
    position: relative;
    width: 1200px;
    height: 950px;
  }
  .card {
    position: absolute;
    width: 640px;
    height: 366px;
    box-shadow: 0 6px 18px rgba(0,0,0,0.18);
  }
  /* Back side */
  .card-back {
    left: 120px;
    top: 84px;
    background: var(--brand-red);
    color: var(--paper);
  }
  .back-mark {
    position: absolute;
    left: 0;
    right: 0;
    top: 104px;
    display: flex;
    justify-content: center;
    align-items: center;
    gap: 14px;
  }
  .back-mark .mark-square {
    width: 30px;
    height: 30px;
    background: var(--paper);
  }
  .back-mark .mark-name {
    font-weight: 900;
    font-size: 46px;
    letter-spacing: 3px;
    color: var(--paper);
  }
  .credentials {
    position: absolute;
    left: 0;
    right: 0;
    top: 226px;
    text-align: center;
    font-weight: 400;
    font-size: 17px;
    letter-spacing: 1.5px;
  }
  .credentials-rule {
    position: absolute;
    left: 220px;
    width: 200px;
    top: 258px;
    height: 1px;
    background: linear-gradient(to right, transparent, rgba(255,255,255,0.8), transparent);
  }
  .social {
    position: absolute;
    left: 0;
    right: 0;
    top: 266px;
    display: flex;
    justify-content: center;
    gap: 8px;
  }
  .social span {
    width: 16px;
    height: 16px;
    border-radius: 50%;
    background: var(--paper);
  }
  /* Front side */
  .card-front {
    left: 440px;
    top: 500px;
    background: var(--paper);
    color: var(--ink);
  }
  .front-logo {
    position: absolute;
    left: 50px;
    top: 166px;
    display: flex;
    align-items: center;
    gap: 12px;
  }
  .front-logo .mark-square {
    width: 22px;
    height: 22px;
    background: var(--brand-red);
  }
  .front-logo .mark-name {
    font-weight: 900;
    font-size: 50px;
    letter-spacing: 2px;
    color: var(--ink);
  }
  .divider {
    position: absolute;
    left: 352px;
    top: 78px;
    width: 2px;
    height: 210px;
    background: var(--rule);
  }
  .divider::before {
    content: "";
    position: absolute;
    left: -1px;
    top: 0;
    width: 4px;
    height: 44px;
    background: var(--brand-red);
  }
  .contact-block {
    position: absolute;
    left: 380px;
    top: 78px;
  }
  .person-name {
    margin: 0;
    font-weight: 700;
    font-size: 24px;
    color: var(--ink);
  }
  .person-role {
    margin: 2px 0 18px;
    font-size: 16px;
    color: var(--brand-red);
  }
  .contact-list {
    list-style: none;
    margin: 0;
    padding: 0;
  }
  .contact-list li {
    display: flex;
    align-items: center;
    gap: 9px;
    font-size: 15px;
    color: var(--ink-soft);
    height: 24px;
  }
  .contact-list svg {
    width: 13px;
    height: 13px;
    fill: var(--ink-soft);
    flex: none;
  }
</style>
</head>
<body>
<main class="canvas">

  <section class="card card-back" aria-label="Business card, back">
    <div class="back-mark">
      <span class="mark-square"></span>
      <span class="mark-name">DULOM</span>
    </div>
    <div class="credentials">LICENSED | INSURED | BONDED</div>
    <div class="credentials-rule"></div>
    <div class="social" aria-label="Social media">
      <span></span><span></span><span></span>
    </div>
  </section>

  <section class="card card-front" aria-label="Business card, front">
    <div class="front-logo">
      <span class="mark-square"></span>
      <span class="mark-name">DULOM</span>
    </div>
    <div class="divider"></div>
    <div class="contact-block">
      <h1 class="person-name">Karim Feltous</h1>
      <p class="person-role">CEO / General Contractor</p>
      <ul class="contact-list">
        <li>
          <svg viewBox="0 0 16 16" aria-hidden="true"><path d="M3.5 1 6 4 4.6 5.8c.9 2 2.6 3.7 4.6 4.6L11 9l3 2.5-1.4 2.8C7 14 2 9 1.7 2.4z"/></svg>
          1-888-DULOM-47
        </li>
        <li>
          <svg viewBox="0 0 16 16" aria-hidden="true"><path d="M4 0h8a1 1 0 0 1 1 1v14a1 1 0 0 1-1 1H4a1 1 0 0 1-1-1V1a1 1 0 0 1 1-1zm1 2v10h6V2zm3 11a1 1 0 1 0 0 2 1 1 0 0 0 0-2z"/></svg>
          317-555-0193
        </li>
        <li>
          <svg viewBox="0 0 16 16" aria-hidden="true"><path d="M0 3h16v10H0zm1.5 1.2L8 9l6.5-4.8V4h-13z"/></svg>
          info@dulomhome.com
        </li>
        <li>
          <svg viewBox="0 0 16 16" aria-hidden="true"><path d="M8 0a8 8 0 1 0 0 16A8 8 0 0 0 8 0zm-1 1.6v2.9H4.2A6.5 6.5 0 0 1 7 1.6zm2 0a6.5 6.5 0 0 1 2.8 2.9H9zM3.6 6H7v4H3.6a6.4 6.4 0 0 1 0-4zM9 6h3.4a6.4 6.4 0 0 1 0 4H9zm-4.8 5.5H7v2.9a6.5 6.5 0 0 1-2.8-2.9zm4.8 0h2.8A6.5 6.5 0 0 1 9 14.4z"/></svg>
          www.dulomhome.com
        </li>
      </ul>
    </div>
  </section>

</main>
</body>
</html>
```